Simple and Clean business card design

We would like the design to be simple clean and to incorporate our colors.

We are open to your design and talent, we have the dots in our logo as we think of it as data points and we connect data points for people.

We are open to see the great creative and clean design you bring to the table

Contact Information for Business Card

please include: name, position, email, phone and website

Font styles to use
Sans Serif

Requirements
Must have
• my colors incorporated, simplicity
Nice to have
• lots of white space, simplicity
Should not have
• complexicity/ complex art

```html
<!DOCTYPE html>
<html lang="en">
<head>
<meta charset="utf-8">
<title>Tessly business card</title>
<link href="https://fonts.googleapis.com/css2?family=Jost:wght@400;600&display=swap" rel="stylesheet">
<style>
  :root {
    --bg: #dcdcdc;
    --card: #ffffff;
    --ink: #141414;
    --text: #3a3a3a;
    --yellow: #f8bd12;
    --green: #2ea65a;
    --red: #ef5450;
    --blue: #5f87c7;
  }
  * { box-sizing: border-box; margin: 0; padding: 0; }
  html, body {
    width: 1200px; height: 1017px; overflow: hidden;
    background: var(--bg);
    font-family: 'Jost', sans-serif;
  }
  .card {
    position: absolute;
    left: 278px;
    width: 644px; height: 367px;
    background: var(--card);
    border-radius: 28px;
    overflow: hidden;
  }
  .card--front { top: 97px; }
  .card--back { top: 519px; }

  .accent-bar {
    position: absolute; left: 0; top: 63px;
    width: 14px; height: 38px;
    background: var(--yellow);
  }
  .company {
    position: absolute; left: 27px; top: 55px;
    font-weight: 600; font-size: 25px; letter-spacing: 0.3px;
    color: var(--green);
  }
  .role {
    position: absolute; left: 27px; top: 85px;
    font-size: 16.5px; color: var(--text);
  }
  .contact {
    position: absolute; left: 26px; top: 266px;
    list-style: none;
  }
  .contact li {
    display: flex; align-items: center;
    height: 23.3px;
    font-size: 16.5px; color: var(--text);
  }
  .contact svg { width: 13px; height: 13px; margin-right: 7px; fill: var(--green); }

  .wordmark {
    position: absolute;
    display: flex; align-items: center;
    font-weight: 600; color: var(--ink);
    line-height: 1;
  }
  .wordmark .dot { border-radius: 50%; background: var(--green); }
  .wordmark--small { right: 32px; top: 262px; font-size: 60px; }
  .wordmark--small .dot { width: 18px; height: 18px; margin-right: 12px; }
  .wordmark--large { left: 50%; top: 50%; transform: translate(-50%, -50%); font-size: 110px; }
  .wordmark--large .dot { width: 32px; height: 32px; margin-right: 20px; }
</style>
</head>
<body>
  <section class="card card--front">
    <div class="accent-bar"></div>
    <h1 class="company">TESSLY.IO</h1>
    <p class="role">Founder/ CEO</p>
    <ul class="contact">
      <li>
        <svg viewBox="0 0 24 24" aria-hidden="true"><path d="M6.6 10.8a15.2 15.2 0 0 0 6.6 6.6l2.2-2.2a1 1 0 0 1 1-.25 11.4 11.4 0 0 0 3.6.57 1 1 0 0 1 1 1V20a1 1 0 0 1-1 1A17 17 0 0 1 3 4a1 1 0 0 1 1-1h3.5a1 1 0 0 1 1 1c0 1.25.2 2.45.57 3.57a1 1 0 0 1-.25 1z"/></svg>
        555-014-2290
      </li>
      <li>
        <svg viewBox="0 0 24 24" aria-hidden="true"><path d="M2 5h20v14H2z M3.5 6.5 12 13l8.5-6.5v-.01H3.5z" fill-rule="evenodd"/></svg>
        nora.bell@tessly.io
      </li>
      <li>
        <svg viewBox="0 0 24 24" aria-hidden="true"><path d="M12 2a10 10 0 1 0 0 20 10 10 0 0 0 0-20zm-1 17.9A8 8 0 0 1 4.2 10.2L9 15v1a2 2 0 0 0 2 2zm6.9-2.5A2 2 0 0 0 16 16h-1v-3a1 1 0 0 0-1-1H8v-2h2a1 1 0 0 0 1-1V7h2a2 2 0 0 0 2-2v-.4a8 8 0 0 1 2.9 12.8z"/></svg>
        www.Tessly.io
      </li>
    </ul>
    <div class="wordmark wordmark--small"><span class="dot"></span>Tessly</div>
  </section>

  <section class="card card--back">
    <div class="wordmark wordmark--large"><span class="dot"></span>Tessly</div>
  </section>
</body>
</html>
```